wealth management firm, professional group, new model

we have a logo that works but we need a card, white background using our colors...clean look

our tag line if can be used in

The Bridge From Client to Owner

```html
<!DOCTYPE html>
<html lang="en">
<head>
<meta charset="utf-8">
<title>Arcova Wealth Partners – Business Card</title>
<link href="https://fonts.googleapis.com/css2?family=Montserrat:wght@300;400;700&display=swap" rel="stylesheet">
<style>
  :root {
    --navy: #2b3f66;
    --navy-deep: #1f2e4d;
    --navy-light: #3a5283;
    --ink: #4a5a78;
    --paper: #ffffff;
    --stage: #e4e5e6;
    --rule: #8a9bbd;
  }
  * { margin: 0; padding: 0; box-sizing: border-box; }
  html, body {
    width: 1200px; height: 800px; overflow: hidden;
    background: var(--stage);
    font-family: "Montserrat", sans-serif;
  }
  .sheet {
    width: 1200px; height: 800px;
    display: flex; align-items: center; justify-content: center; gap: 60px;
  }
  .card {
    width: 520px; height: 298px;
    position: relative; overflow: hidden;
    box-shadow: 0 10px 30px rgba(0,0,0,0.12);
  }

  /* Front side */
  .card--front { color: var(--paper); }
  .card__pattern {
    position: absolute; inset: 0;
    background: linear-gradient(135deg, var(--navy-deep) 0%, var(--navy) 50%, var(--navy-light) 100%);
  }
  .front__content {
    position: relative; height: 100%;
    display: flex; flex-direction: column; align-items: center; justify-content: center;
    text-align: center;
  }
  .front__name {
    display: flex; align-items: center; gap: 10px;
    font-weight: 400; font-size: 26px; line-height: 1.2;
  }
  .front__dot {
    width: 10px; height: 10px; border-radius: 50%; background: var(--paper);
  }
  .front__tagline {
    font-weight: 300; font-size: 11px; letter-spacing: 2px;
    text-transform: uppercase; margin-top: 18px;
  }

  /* Back side */
  .card--back { background: var(--paper); color: var(--ink); }
  .back__person { position: absolute; left: 40px; top: 38px; }
  .back__name {
    font-weight: 700; font-size: 17px; color: var(--navy);
    text-transform: uppercase; letter-spacing: 0.3px;
  }
  .back__role { font-weight: 400; font-size: 13px; margin-top: 2px; }

  .back__contacts {
    position: absolute; left: 40px; top: 132px;
    list-style: none; font-size: 12.5px; font-weight: 400;
  }
  .back__contacts li {
    display: flex; align-items: center; gap: 8px; height: 19px;
  }
  .icon { width: 12px; height: 12px; fill: none; stroke: var(--navy); stroke-width: 1.6; }
  .icon--solid { fill: var(--navy); stroke: none; }

  .back__rule {
    position: absolute; left: 40px; right: 40px; top: 206px;
    border: 0; border-top: 1px solid var(--rule);
  }
  .back__address {
    position: absolute; left: 40px; top: 222px;
    display: flex; align-items: center; gap: 8px;
    font-size: 12.5px;
  }

  .back__brand {
    position: absolute; right: 40px; top: 150px;
    display: flex; align-items: center; gap: 8px;
    color: var(--navy); font-weight: 400; font-size: 15px;
  }
  .back__brand-dot {
    width: 8px; height: 8px; border-radius: 50%; background: var(--navy);
  }
</style>
</head>
<body>
<main class="sheet">

  <section class="card card--front">
    <div class="card__pattern" role="img" aria-label="Navy low-poly faceted background pattern"></div>
    <div class="front__content">
      <div class="front__name"><span class="front__dot"></span>Arcova Wealth Partners</div>
      <div class="front__tagline">The Bridge From Client to Owner</div>
    </div>
  </section>

  <section class="card card--back">
    <div class="back__person">
      <div class="back__name">Marco Bellini</div>
      <div class="back__role">Brand Manager</div>
    </div>

    <ul class="back__contacts">
      <li>
        <svg class="icon icon--solid" viewBox="0 0 12 12" aria-hidden="true"><path d="M2.5 0.5 L4.5 0.5 L5 3.2 L3.8 4.2 C4.5 5.8 6 7.3 7.8 8.2 L8.8 7 L11.5 7.5 L11.5 9.5 C11.5 10.8 10.5 11.5 9.5 11.5 C4.5 11 1 7.5 0.5 2.5 C0.5 1.3 1.3 0.5 2.5 0.5 Z"/></svg>
        <span>+39.312.555.0148</span>
      </li>
      <li>
        <svg class="icon" viewBox="0 0 12 12" aria-hidden="true"><rect x="0.8" y="2.3" width="10.4" height="7.4"/><path d="M0.8 2.3 L6 6.6 L11.2 2.3"/></svg>
        <span>info@arcovamail.com</span>
      </li>
      <li>
        <svg class="icon" viewBox="0 0 12 12" aria-hidden="true"><circle cx="6" cy="6" r="5.2"/><ellipse cx="6" cy="6" rx="2.2" ry="5.2"/><path d="M0.8 6 H11.2 M1.6 3.4 H10.4 M1.6 8.6 H10.4"/></svg>
        <span>www.arcovaweb.com</span>
      </li>
    </ul>

    <hr class="back__rule">

    <div class="back__address">
      <svg class="icon icon--solid" viewBox="0 0 12 12" aria-hidden="true"><path d="M6 0.5 C3.6 0.5 2 2.2 2 4.4 C2 7.2 6 11.5 6 11.5 C6 11.5 10 7.2 10 4.4 C10 2.2 8.4 0.5 6 0.5 Z M6 3 A1.4 1.4 0 1 1 6 5.8 A1.4 1.4 0 1 1 6 3 Z" fill-rule="evenodd"/></svg>
      <span>Via Fiorita 8 20121 Milano, USA</span>
    </div>

    <div class="back__brand">
      <span class="back__brand-dot"></span>
      <span>Arcova Wealth Partners</span>
    </div>
  </section>

</main>
</body>
</html>
```